Business card for Luxury Portable Restroom Trailer company

We are a Luxury Portable Restroom Trailer Company Called FALCRIDGE HIRES. Based in Orange County California. We provide portable restroom trailers for events, such as, Weddings, Concerts, Charity events, Sporting events, Tournaments, Corporate events, ect. We rent and Sell the Luxury restrooms. Our colors are white, grey, and Orange. As you will see in the logo we uploaded.
There are 2 people in the company so the names and titles will change for the 3 people but card will remain the same. Here is the information for each Person: Dwight Penner CFO 555 318-0476
next Person: Leon Marchetti VP 555 318-0476
Next Person: Owen Marchetti CEO 555 318-0476
Information to include on the card: Luxury Restroom Trailers Rental and Sales. Weddings, Concerts, Charity, Sporting and Corp. Events.

```html
<!DOCTYPE html>
<html lang="en">
<head>
<meta charset="utf-8">
<title>Falcridge Hires – Business Card</title>
<link href="https://fonts.googleapis.com/css2?family=Mulish:wght@400;600;800;900&display=swap" rel="stylesheet">
<style>
  :root{
    --bg:#2a2a2b;
    --card-grey:#5d5d5f;
    --card-grey-dark:#48484a;
    --card-grey-light:#6e6e70;
    --panel:#f1f1f1;
    --orange:#e8702a;
    --ink:#4a4a4c;
    --white:#ffffff;
  }
  *{box-sizing:border-box;margin:0;padding:0}
  html,body{width:1200px;height:1200px;overflow:hidden}
  body{
    background:var(--bg);
    font-family:"Mulish",Arial,sans-serif;
    display:flex;flex-direction:column;align-items:center;justify-content:center;gap:60px;
  }
  .card{
    position:relative;width:700px;height:400px;overflow:hidden;
    background:radial-gradient(ellipse at 50% 45%,var(--card-grey-light) 0%,var(--card-grey) 45%,var(--card-grey-dark) 100%);
    box-shadow:0 18px 40px rgba(0,0,0,.45);
  }
  /* front */
  .card-front{display:flex;align-items:center;justify-content:center}
  .brand{display:flex;align-items:center;gap:22px}
  .brand-mark{width:54px;height:54px;background:var(--orange)}
  .brand-name{
    color:var(--white);font-weight:900;font-size:58px;letter-spacing:3px;line-height:1;
  }
  /* back */
  .back-emblem{
    position:absolute;left:380px;top:28px;width:110px;height:110px;
    border:5px solid var(--orange);border-radius:50%;
  }
  .back-brand{
    position:absolute;left:500px;top:70px;color:var(--orange);
    font-weight:800;font-size:18px;letter-spacing:2px;
  }
  .panel{position:absolute;background:var(--panel)}
  .panel-name{left:0;top:170px;width:370px;height:110px;padding:18px 40px 0 0;text-align:right}
  .person-name{color:var(--orange);font-weight:800;font-size:30px;line-height:1.1}
  .person-title{color:var(--ink);font-weight:400;font-size:17px;margin-top:10px;letter-spacing:1px}
  .panel-contact{left:385px;top:170px;width:315px;height:160px;padding:30px 0 0 40px}
  .contact-row{display:flex;align-items:center;gap:12px;color:var(--ink);font-size:16px;line-height:1;margin-bottom:16px}
  .contact-row svg{width:16px;height:16px;flex:none;fill:var(--orange)}
  .services{
    position:absolute;left:30px;top:298px;width:340px;text-align:right;
    color:var(--panel);font-size:15px;line-height:1.55;
  }
</style>
</head>
<body>
  <section class="card card-front" aria-label="Card front">
    <div class="brand">
      <span class="brand-mark"></span>
      <span class="brand-name">FALCRIDGE HIRES</span>
    </div>
  </section>

  <section class="card card-back" aria-label="Card back">
    <div class="back-emblem"></div>
    <div class="back-brand">FALCRIDGE HIRES</div>

    <div class="panel panel-name">
      <p class="person-name">Dwight Penner</p>
      <p class="person-title">CFO</p>
    </div>

    <div class="panel panel-contact">
      <p class="contact-row">
        <svg viewBox="0 0 24 24"><path d="M6.6 10.8a15 15 0 0 0 6.6 6.6l2.2-2.2c.3-.3.7-.4 1-.2 1.1.4 2.3.6 3.6.6.6 0 1 .4 1 1V20c0 .6-.4 1-1 1A17 17 0 0 1 3 4c0-.6.4-1 1-1h3.5c.6 0 1 .4 1 1 0 1.3.2 2.5.6 3.6.1.3 0 .7-.2 1z"/></svg>
        555 318-0476
      </p>
      <p class="contact-row">
        <svg viewBox="0 0 24 24"><path d="M2 5h20v14H2z M2 5l10 8 10-8" fill="none" stroke="#e8702a" stroke-width="2.4"/></svg>
        info@falcridgehires.com
      </p>
      <p class="contact-row">
        <svg viewBox="0 0 24 24"><circle cx="12" cy="12" r="10"/><path d="M2 12h20M12 2c3 3 3 17 0 20M12 2c-3 3-3 17 0 20" stroke="#f1f1f1" stroke-width="1.6" fill="none"/></svg>
        www.falcridgehires.com
      </p>
    </div>

    <p class="services">Luxury Restroom | Trailers Rental and Sales<br>Weddings | Concerts | Charity | Sporting | Corp. Events</p>
  </section>
</body>
</html>
```